Create a flyer for our party getaway to Ibiza.

'The Drifted Ibiza Getaway'

Friday 14th July - Monday 17th July

DJ Varro & DJ Mercer brings together a jam-packed weekend schedule full of the best urban parties in Ibiza.

What's included?

4 Nights Of Entertainment
6 Parties In Total
1 Boat Party
1 Pool Party
2 Superclub Parties
1 Indoor Water Party
Bottomless Drinks (Boat Party Only)
An unbelievable experience
1 unbeatable price.

All this for 140€ (you save 50€ when you book with us)

Tickets avaialble from Tixlane & Gobrino

Target Market(s)

holiday goers

Industry/Entity Type

party, events, club, hip hop

Requirements
Must have
• good vibes
Nice to have
• nice catchy looking title

```html
<!DOCTYPE html>
<html lang="en">
<head>
<meta charset="utf-8">
<title>The Drifted Ibiza Getaway – Flyer</title>
<link rel="stylesheet" href="https://fonts.googleapis.com/css2?family=Russo+One&family=Montserrat:wght@800;900&family=Poppins:wght@500;600;700&family=Yellowtail&display=swap">
<style>
  :root{
    --page:#e2e2e4;
    --night:#07051a;
    --indigo:#1a0f6e;
    --violet:#5a1fd1;
    --magenta:#e021d8;
    --hot-pink:#ff3fa6;
    --neon-pink:#f25cf0;
    --cyan:#17e3f0;
    --sky:#2f8bff;
    --gold:#ffc81a;
    --white:#ffffff;
    --orange:#ff6a1a;
    --list-pink:#e93fe6;
  }
  *{margin:0;padding:0;box-sizing:border-box}
  html,body{width:1200px;height:2318px;overflow:hidden;background:var(--page)}
  .flyer{
    position:absolute;left:50px;top:448px;width:1100px;height:1422px;overflow:hidden;
    background:
      radial-gradient(ellipse 420px 360px at 930px 720px, rgba(255,40,120,.75), transparent 70%),
      radial-gradient(ellipse 380px 420px at 120px 760px, rgba(30,60,200,.55), transparent 70%),
      radial-gradient(ellipse 700px 520px at 550px 300px, rgba(120,40,230,.7), transparent 70%),
      linear-gradient(180deg, var(--indigo) 0%, #2a0f8a 35%, #1a0a5a 62%, var(--night) 74%, var(--night) 100%);
    box-shadow:0 20px 40px rgba(0,0,0,.35);
    font-family:"Poppins",sans-serif;color:var(--white);
  }
  .flyer > *{position:absolute}
  .neon-frame{left:0;top:0;width:1100px;height:700px}
  .lower-shade{left:0;top:995px;width:1100px;height:427px;
    background:linear-gradient(180deg, rgba(40,10,110,.85), var(--night) 45%)}
  .title-kicker{left:0;width:1100px;top:52px;text-align:center;
    font-family:"Russo One",sans-serif;font-size:62px;letter-spacing:1px;line-height:1;
    transform:skewX(-14deg);
    background:linear-gradient(90deg,var(--cyan),var(--sky) 60%,#6a7bff);
    -webkit-background-clip:text;background-clip:text;color:transparent}
  .title-main{left:0;width:1100px;top:118px;text-align:center;
    font-family:"Russo One",sans-serif;font-size:150px;letter-spacing:6px;line-height:1;
    transform:skewX(-14deg);
    background:linear-gradient(180deg,#ff9ef5 0%,var(--neon-pink) 45%,var(--magenta) 100%);
    -webkit-background-clip:text;background-clip:text;color:transparent}
  .title-script{left:0;width:1100px;top:210px;text-align:center;
    font-family:"Yellowtail",cursive;font-size:150px;line-height:1.1;color:var(--white);
    text-shadow:0 4px 10px rgba(0,0,0,.45)}
  .dj-photo{left:150px;top:395px;width:730px;height:600px;border-radius:40% 40% 0 0;
    background:radial-gradient(ellipse at 50% 45%, #f3d7f5 0%, #c98fe0 35%, rgba(120,50,200,.6) 65%, transparent 80%)}
  .dj-names{left:0;top:800px;width:1100px;height:200px}
  .dj-word{position:absolute;top:0;font-family:"Montserrat",sans-serif;font-weight:900;font-size:140px;line-height:1;color:var(--white)}
  .dj-word.left{left:290px}
  .dj-word.right{left:626px}
  .amp{position:absolute;left:528px;top:20px;font-family:"Poppins",sans-serif;font-weight:500;font-size:100px;line-height:1;color:var(--white)}
  .dj-script{position:absolute;font-family:"Yellowtail",cursive;font-size:100px;line-height:1}
  .dj-script.varro{left:272px;top:78px;color:var(--gold);text-shadow:0 3px 6px rgba(0,0,0,.5)}
  .dj-script.mercer{left:620px;top:70px;color:var(--magenta);text-shadow:0 3px 6px rgba(0,0,0,.5)}
  .tagline{left:79px;top:1001px;width:940px;height:54px;border:2px solid var(--white);
    display:flex;align-items:center;justify-content:center;font-weight:600;font-size:20.5px}
  .includes{left:84px;top:1079px;list-style:none}
  .includes li{display:flex;align-items:center;gap:6px;line-height:1}
  .includes .main{font-size:20px;font-weight:600;color:var(--list-pink);height:25px}
  .includes .sub{font-size:16.5px;font-weight:500;color:var(--white);height:19.5px;padding-left:26px}
  .includes svg{flex:none}
  .price{left:84px;top:1292px;font-size:41px;font-weight:600;color:var(--gold);line-height:1}
  .saving{left:84px;top:1341px;font-size:17.5px;font-weight:500}
  .dates{left:469px;top:1087px}
  .date-row{display:flex;align-items:center;height:49px;margin-bottom:12px;
    font-family:"Poppins",sans-serif;font-weight:700;font-size:48px;line-height:1}
  .day{background:var(--cyan);color:var(--indigo);padding:0 6px;height:49px;display:flex;align-items:center;margin-right:18px}
  .date-row sup{font-size:24px;align-self:flex-start;margin-top:2px}
  .date-row .to{font-size:32px;font-weight:500;margin-left:14px;align-self:flex-end;color:var(--white)}
  .tickets-label{left:466px;top:1226px;font-size:27px;font-weight:600}
  .vendor{display:flex;align-items:center;gap:12px;font-family:"Poppins",sans-serif;font-weight:700;font-size:40px;color:var(--white);line-height:1}
  .vendor .mark{width:30px;height:30px;background:var(--orange);border-radius:4px}
  .vendor.tixlane{left:490px;top:1285px}
  .vendor.gobrino{left:788px;top:1285px}
</style>
</head>
<body>
<main class="flyer">
  <svg class="neon-frame" viewBox="0 0 1100 700" aria-hidden="true">
    <defs>
      <filter id="glow" x="-20%" y="-20%" width="140%" height="140%">
        <feGaussianBlur stdDeviation="6" result="b"/>
        <feMerge><feMergeNode in="b"/><feMergeNode in="SourceGraphic"/></feMerge>
      </filter>
    </defs>
    <g filter="url(#glow)" fill="none" stroke-linejoin="round">
      <polygon points="60,35 1040,35 547,560" stroke="#7a5cff" stroke-width="3" opacity=".7"/>
      <polygon points="169,221 961,221 547,521" stroke="#f2b8ff" stroke-width="5"/>
    </g>
  </svg>

  <div class="title-kicker">THE DRIFTED</div>
  <div class="title-main">IBIZA</div>
  <div class="title-script">Getaway</div>

  <div class="dj-photo" role="img" aria-label="Photo of the two DJs posing together in white t-shirts"></div>

  <div class="lower-shade"></div>

  <div class="dj-names">
    <span class="dj-word left">DJ</span>
    <span class="amp">&amp;</span>
    <span class="dj-word right">DJ</span>
    <span class="dj-script varro">Varro</span>
    <span class="dj-script mercer">Mercer</span>
  </div>

  <p class="tagline">Brings together a jam-packed weekend schedule full of the best urban parties in Ibiza</p>

  <ul class="includes">
    <li class="main"><svg width="15" height="15" viewBox="0 0 16 16"><rect x="1" y="3" width="12" height="12" fill="none" stroke="#fff" stroke-width="1.6"/><path d="M4 8l3 3 8-9" fill="none" stroke="#fff" stroke-width="2"/></svg>4 Nights Of Entertainment</li>
    <li class="main"><svg width="15" height="15" viewBox="0 0 16 16"><rect x="1" y="3" width="12" height="12" fill="none" stroke="#fff" stroke-width="1.6"/><path d="M4 8l3 3 8-9" fill="none" stroke="#fff" stroke-width="2"/></svg>6 Parties In Total</li>
    <li class="sub"><svg width="11" height="11" viewBox="0 0 16 16"><rect x="1" y="3" width="12" height="12" fill="none" stroke="#17e3f0" stroke-width="1.8"/><path d="M4 8l3 3 8-9" fill="none" stroke="#17e3f0" stroke-width="2.2"/></svg>1 Boat Party</li>
    <li class="sub"><svg width="11" height="11" viewBox="0 0 16 16"><rect x="1" y="3" width="12" height="12" fill="none" stroke="#17e3f0" stroke-width="1.8"/><path d="M4 8l3 3 8-9" fill="none" stroke="#17e3f0" stroke-width="2.2"/></svg>1 Pool Party</li>
    <li class="sub"><svg width="11" height="11" viewBox="0 0 16 16"><rect x="1" y="3" width="12" height="12" fill="none" stroke="#17e3f0" stroke-width="1.8"/><path d="M4 8l3 3 8-9" fill="none" stroke="#17e3f0" stroke-width="2.2"/></svg>2 Superclub Parties</li>
    <li class="sub"><svg width="11" height="11" viewBox="0 0 16 16"><rect x="1" y="3" width="12" height="12" fill="none" stroke="#17e3f0" stroke-width="1.8"/><path d="M4 8l3 3 8-9" fill="none" stroke="#17e3f0" stroke-width="2.2"/></svg>1 Indoor Water Party</li>
    <li class="sub"><svg width="11" height="11" viewBox="0 0 16 16"><rect x="1" y="3" width="12" height="12" fill="none" stroke="#17e3f0" stroke-width="1.8"/><path d="M4 8l3 3 8-9" fill="none" stroke="#17e3f0" stroke-width="2.2"/></svg>Bottomless Drinks (Boat Party Only)</li>
    <li class="main"><svg width="15" height="15" viewBox="0 0 16 16"><rect x="1" y="3" width="12" height="12" fill="none" stroke="#fff" stroke-width="1.6"/><path d="M4 8l3 3 8-9" fill="none" stroke="#fff" stroke-width="2"/></svg>An unbelievable experience</li>
    <li class="main"><svg width="15" height="15" viewBox="0 0 16 16"><rect x="1" y="3" width="12" height="12" fill="none" stroke="#fff" stroke-width="1.6"/><path d="M4 8l3 3 8-9" fill="none" stroke="#fff" stroke-width="2"/></svg>1 unbeatable price</li>
  </ul>

  <p class="price">All this for 140€</p>
  <p class="saving">(you save 50€ when you book with us)</p>

  <div class="dates">
    <div class="date-row"><span class="day">FRIDAY</span>14<sup>TH</sup>&nbsp;JULY<span class="to">TO</span></div>
    <div class="date-row"><span class="day">MONDAY</span>17<sup>TH</sup>&nbsp;JULY</div>
  </div>

  <p class="tickets-label">Tickets avaialble from</p>
  <div class="vendor tixlane"><span class="mark"></span>Tixlane</div>
  <div class="vendor gobrino">Gobrino</div>
</main>
</body>
</html>
```